Verlindo Magician

I want the business card for my business to give to people who watch that later I will be employed to show magic here is my website http://www.balsamomagicien.com/I want the interesting design , i am very opened for formal and informal, I watch a lot of design so don't stick to the common shape and form but i hope it can also be produced the thing to write on will be the same as in picture that i will upload , i also will upload the logo for you that so can be easy to useDenis CostilleMagicianMAGICIAN VERLINDO 17 rue des Tilleuls - 25000 BESANÇON contact@verlindoillusions.example tel. 0381 946 157 tel. 0674 219 503

```html
<!DOCTYPE html>
<html lang="fr">
<head>
<meta charset="utf-8">
<title>Verlindo Magician – Business Card</title>
<link rel="stylesheet" href="https://fonts.googleapis.com/css2?family=Open+Sans:wght@400;700&display=swap">
<style>
  :root {
    --backdrop: #999999;
    --card-light: #ffffff;
    --card-dark: #000000;
    --ink: #111111;
    --accent: #e8312f;
    --rule: #bdbdbd;
    --figure-dark: #1a1a1a;
    --figure-light: #f2f2f2;
  }
  html, body {
    margin: 0;
    padding: 0;
    width: 1200px;
    height: 900px;
    overflow: hidden;
    background: var(--backdrop);
    font-family: "Open Sans", Arial, sans-serif;
    color: var(--ink);
  }
  .stage { position: relative; width: 1200px; height: 900px; }

  .card { position: absolute; width: 478px; height: 294px; box-sizing: border-box; }
  .card-front {
    left: 120px; top: 275px;
    background: var(--card-light);
    border-radius: 0 48px 0 48px;
  }
  .card-back {
    left: 607px; top: 274px;
    background: var(--card-dark);
    border-radius: 48px 0 48px 0;
  }

  .portrait-area {
    position: absolute;
    left: 40px; top: 48px;
    width: 125px; height: 162px;
    background: linear-gradient(180deg, var(--figure-dark), #3a3a3a);
    border-radius: 40px 40px 6px 6px;
  }
  .brand-name {
    position: absolute;
    left: 40px; top: 205px;
    width: 125px;
    text-align: center;
    font-size: 23px;
    font-weight: 400;
    letter-spacing: 1px;
    color: var(--ink);
  }
  .divider {
    position: absolute;
    left: 195px; top: 62px;
    width: 1px; height: 170px;
    background: var(--rule);
  }

  .details { position: absolute; left: 219px; top: 58px; }
  .person-name { margin: 0; font-size: 18px; font-weight: 700; line-height: 22px; letter-spacing: .3px; }
  .person-role { margin: 0 0 6px; font-size: 14px; color: var(--accent); line-height: 18px; }
  .contact-list { list-style: none; margin: 0; padding: 0; }
  .contact-list li {
    display: flex; align-items: center; gap: 4px;
    font-size: 13.5px; line-height: 17.3px; white-space: nowrap;
  }
  .contact-list svg { width: 13px; height: 13px; flex: none; }
  .studio { margin-top: 9px; font-size: 13.5px; line-height: 17px; }
  .studio-name { font-weight: 700; letter-spacing: .3px; }

  .back-figure {
    position: absolute;
    left: 168px; top: 61px;
    width: 138px; height: 168px;
    background: linear-gradient(180deg, var(--figure-light), #cfcfcf);
    border-radius: 40px 40px 8px 8px;
  }
</style>
</head>
<body>
<main class="stage">
  <section class="card card-front" aria-label="Card front">
    <div class="portrait-area" role="img" aria-label="Illustration of the magician in a dark suit holding a playing card"></div>
    <div class="brand-name">VERLINDO</div>
    <div class="divider"></div>

    <div class="details">
      <h1 class="person-name">MARC RAVOULET</h1>
      <p class="person-role">Magician</p>
      <ul class="contact-list">
        <li><svg viewBox="0 0 16 16" aria-hidden="true"><path fill="#111" d="M2 6c0-2 3-3 6-3s6 1 6 3v1h-3V5.5H5V7H2zM4 8h8l1.5 5h-11z"/></svg>0381 946 157</li>
        <li><svg viewBox="0 0 16 16" aria-hidden="true"><path fill="#111" d="M2 6c0-2 3-3 6-3s6 1 6 3v1h-3V5.5H5V7H2zM4 8h8l1.5 5h-11z"/></svg>0674 219 503</li>
        <li><svg viewBox="0 0 16 16" aria-hidden="true"><rect x="1.5" y="3.5" width="13" height="9" fill="none" stroke="#111" stroke-width="1.6"/><path d="M1.5 3.5 8 9l6.5-5.5" fill="none" stroke="#111" stroke-width="1.6"/></svg>contact@verlindoillusions.example</li>
        <li><svg viewBox="0 0 16 16" aria-hidden="true"><circle cx="8" cy="8" r="6.5" fill="#111"/><path d="M5 5.5c1.5-.5 2.5.5 2 1.5s-2 1-1.5 2.5M10 10.5c.5-1 1.5-1.5 2-1" fill="none" stroke="#fff" stroke-width="1.2"/></svg>www.verlindoillusions.example</li>
      </ul>
      <div class="studio">
        <div class="studio-name">MAGICIAN VERLINDO</div>
        <div>17 rue des Tilleuls - 25000</div>
        <div>BESANÇON</div>
      </div>
    </div>
  </section>

  <section class="card card-back" aria-label="Card back">
    <div class="back-figure" role="img" aria-label="White silhouette illustration of the magician holding a playing card"></div>
  </section>
</main>
</body>
</html>
```